Onlineshop for a new Golf Brand (Balls, Tees, Marker & Towels)

We are seeking a distinctive and captivating design for our online store, "Amber Falcon Golfing." The store (shopify) will focus on selling a curated selection of golf accessories, including balls, tees, markers, and towels. Given that we will have a limited product range (around 10 products), the design should emphasize individual product detail and the brand's ethos. We place a high emphasis on an intuitive user experience and a design that resonates with the values and aesthetics of our brand.

Design & Aesthetics:

Style Direction: Minimalistic with a touch of luxury. The design should accentuate the premium nature and quality of our products.
Color Scheme: Primary colors should be aligned with our brand logo and the provided design assets. We prefer a mix of calm and neutral shades, complemented by purposeful accents that draw attention to specific areas.
Typography: A contemporary, clear, and legible typeface suitable for both headlines and body text. Typography should complement the overall design aesthetic without overshadowing it.
Imagery: With a limited product range, product images should be the centerpiece. They should be large, clearly visible, with the option to zoom in for a closer look at details. Incorporating additional lifestyle shots showcasing the products in action can enhance the shopping experience.
UI/UX Elements: Clear and distinguishable call-to-action buttons, intuitive navigation elements, and understandable icons. The checkout process should be streamlined and swift, ensuring customers have a frictionless experience.

I added some mockups of the balls and their packaging as well as the main logo (Falcon) and the alternative one (letters).

```html
<!DOCTYPE html>
<html lang="en">
<head>
<meta charset="utf-8">
<title>Amber Falcon Golfing — Home</title>
<link rel="stylesheet" href="https://fonts.googleapis.com/css2?family=Aldrich&family=Montserrat:wght@400;500;700&family=Open+Sans:wght@600;700&display=swap">
<style>
:root{
  --brand:#8a0202;
  --brand-dark:#6b0909;
  --ink:#111111;
  --text:#333333;
  --white:#ffffff;
  --line:#e6e6e6;
  --badge:#c4c4c4;
}
*{box-sizing:border-box;margin:0;padding:0}
html,body{width:1200px;height:3904px;overflow:hidden;background:var(--white)}
body{position:relative;font-family:'Montserrat',sans-serif;color:var(--text)}
.abs{position:absolute}
.display{font-family:'Aldrich',sans-serif;color:var(--ink);font-weight:400}
.btn{position:absolute;display:flex;align-items:center;justify-content:center;background:var(--brand);color:var(--white);border-radius:22px;font-size:16px}

/* top bar */
.topbar{left:0;top:0;width:1200px;height:64px;background:var(--brand-dark)}
.social{top:22px;width:22px;height:22px;border-radius:50%;background:#f2f2f2}
.lang{right:48px;top:22px;color:var(--white);font-size:15px}
.shipbar{left:0;top:64px;width:1200px;height:54px;background:var(--brand);color:var(--white);font-family:'Open Sans',sans-serif;font-weight:700;font-size:15px;display:flex;align-items:center;justify-content:center}

/* header */
.header{left:0;top:118px;width:1200px;height:105px;border-bottom:1px solid var(--line)}
.nav a{position:absolute;top:43px;font-size:15px;color:var(--text);text-decoration:none}
.nav a.active{border-bottom:2px solid var(--brand);padding-bottom:2px}
.brand-name{left:0;width:1200px;top:60px;text-align:center;color:var(--brand);font-size:15px;font-weight:500}

/* hero */
.hero{left:0;top:223px;width:1200px;height:595px;
  background:
    radial-gradient(ellipse 260px 200px at 840px 400px,rgba(255,244,214,.95),rgba(255,236,190,.35) 55%,transparent 100%),
    linear-gradient(180deg,#dfeaf0 0%,#cbdde6 28%,#a9bcbe 42%,#4d5d3c 58%,#2c3a22 74%,#4f7130 88%,#7fa648 100%)}
.hero-kicker{left:0;width:1200px;top:357px;text-align:center;font-size:37px}
.hero-title{left:0;width:1200px;top:400px;text-align:center;font-size:46px}

/* popular */
.shop-all{left:897px;top:901px;font-size:18px;color:var(--ink)}
.promo{left:55px;top:980px;width:1090px;height:364px;
  background:
    radial-gradient(circle at 27% 42%,rgba(245,247,250,.95) 0,rgba(235,240,245,.8) 70px,rgba(120,160,80,.0) 120px),
    linear-gradient(160deg,#5f9a34,#3a7420 45%,#2e6016 70%,#4a8526)}
.promo-title{left:505px;top:1072px;font-family:'Open Sans',sans-serif;font-weight:700;font-size:44px;color:var(--white);letter-spacing:-.5px}

/* product card */
.card{left:45px;top:1518px;width:1110px;height:623px;background:var(--white);box-shadow:0 0 10px rgba(0,0,0,.15)}
.thumb{left:83px;width:105px;height:77px;border:1px solid #ddd}
.main-shot{left:174px;top:1712px;width:334px;height:351px;
  background:radial-gradient(ellipse at 45% 50%,#ffffff 0,#f3f1f1 45%,#e4dcdc 75%,#ffffff 100%)}
.p-title{left:600px;top:1560px;font-size:30px}
.p-desc{left:600px;top:1617px;width:500px;font-size:15px;line-height:29px}
.p-price{left:600px;top:1696px;font-family:'Open Sans',sans-serif;font-weight:700;font-size:29px;color:var(--ink)}
.label{left:600px;font-size:14px}
.swatch{top:1785px;width:25px;height:25px;border-radius:50%}
.qty{left:600px;top:1878px;width:74px;height:24px;border:1px solid #999;border-radius:12px;font-size:13px;display:flex;justify-content:space-around;align-items:center}
.details{left:600px;top:2069px;font-size:15px;color:var(--ink);display:flex;align-items:center;gap:8px}

/* golf products */
.gp-text{left:63px;top:2375px;width:500px;font-size:16px;line-height:29px;text-align:justify}

/* testimonials */
.testimonials{left:0;top:2921px;width:1200px;height:417px;background:var(--brand)}
.quote{width:392px;text-align:center;color:var(--white)}
.quote p{font-size:16px;line-height:29px;margin-top:20px}
.quote b{display:block;margin-top:14px;font-weight:700;font-size:16px}

/* partner badges */
.badge{top:3442px;width:110px;height:110px;border-radius:50%;background:var(--badge)}

/* footer */
.footer{left:0;top:3644px;width:1200px;height:260px;background:var(--brand)}
.news{left:115px;top:3740px;font-family:'Aldrich',sans-serif;color:var(--white);font-size:17px}
.email{left:594px;top:3712px;width:494px;height:57px;background:rgba(255,255,255,.25);color:var(--white);font-size:16px;padding-left:16px;display:flex;align-items:center}
.copy{left:0;width:1200px;top:3848px;text-align:center;color:var(--white);font-size:14px}
</style>
</head>
<body>

<!-- top bar -->
<div class="abs topbar"></div>
<span class="abs social" style="left:52px"></span>
<span class="abs social" style="left:89px"></span>
<span class="abs social" style="left:126px"></span>
<span class="abs social" style="left:165px"></span>
<span class="abs lang">English ⌄</span>
<div class="abs shipbar">Free shipping for orders of $300 +</div>

<!-- header -->
<header class="abs header">
  <nav class="nav">
    <a class="active" style="left:48px">Home</a>
    <a style="left:120px">Shop</a>
    <a style="left:184px">About us</a>
    <a style="left:275px">Blog</a>
    <a style="left:336px">Contact</a>
  </nav>
  <div class="abs brand-name">Amber Falcon Golfing</div>
  <svg class="abs" style="left:1086px;top:42px" width="24" height="24" viewBox="0 0 24 24" fill="none" stroke="#111" stroke-width="2.5"><circle cx="10" cy="10" r="7"/><path d="M15 15l7 7"/></svg>
  <svg class="abs" style="left:1126px;top:42px" width="26" height="24" viewBox="0 0 26 24" fill="#111"><path d="M0 2h5l4 13h13l3-10H8l-1-3z"/><circle cx="11" cy="20" r="2.3"/><circle cx="20" cy="20" r="2.3"/></svg>
</header>

<!-- hero -->
<div class="abs hero" role="img" aria-label="Golfer finishing a swing on a sunlit course lined with pine trees"></div>
<div class="abs display hero-kicker">Welcome To</div>
<div class="abs display hero-title">Amber Falcon Golfing</div>
<div class="btn" style="left:523px;top:483px;width:154px;height:43px">Shop Now</div>

<!-- popular now -->
<h2 class="abs display" style="left:114px;top:890px;font-size:38px">Popular now</h2>
<div class="abs shop-all">Shop all products</div>
<svg class="abs" style="left:1064px;top:901px" width="24" height="24" viewBox="0 0 24 24"><circle cx="12" cy="12" r="12" fill="#8a0202"/><path d="M10 7l5 5-5 5" stroke="#fff" stroke-width="2.5" fill="none"/></svg>
<div class="abs promo" role="img" aria-label="Branded golf ball resting on green grass"></div>
<div class="abs promo-title">Buy Golf Balls at 10% Off</div>
<div class="btn" style="left:503px;top:1154px;width:153px;height:41px">Shop Now</div>

<!-- best value -->
<h2 class="abs display" style="left:0;width:1200px;text-align:center;top:1425px;font-size:30px">Best Value</h2>
<section class="abs card"></section>
<div class="abs thumb" style="top:1564px;background:linear-gradient(90deg,#f4f4f4 0,#e8e2e2 40%,#3a3a3a 70%,#f0f0f0 100%)" role="img" aria-label="Ball tube with drawstring bag"></div>
<div class="abs thumb" style="top:1656px;background:linear-gradient(135deg,#fafafa,#e9e3e3 60%,#f7f7f7)" role="img" aria-label="Ball tube with lid"></div>
<div class="abs main-shot" role="img" aria-label="White and red golf ball tube with black drawstring and round lid"></div>
<h3 class="abs display p-title">Golf Bag</h3>
<p class="abs p-desc">Lorem ipsum dolor sit amet, consectetur adipiscing elit, sed do eiusmod tempor incididunt ut labore et dolore magna aliqua.</p>
<div class="abs p-price">$85.00</div>
<span class="abs label" style="top:1750px">Color:</span>
<span class="abs swatch" style="left:600px;background:#8a0202"></span>
<span class="abs swatch" style="left:632px;background:#6fcdc3"></span>
<span class="abs swatch" style="left:664px;background:#e8b84a"></span>
<span class="abs swatch" style="left:697px;background:#4c5a3d"></span>
<span class="abs swatch" style="left:731px;background:#d39b9b"></span>
<span class="abs label" style="top:1838px">Quantity:</span>
<div class="abs qty"><span>-</span><span>1</span><span>+</span></div>
<div class="btn" style="left:600px;top:1939px;width:283px;height:41px">Add To Cart</div>
<div class="btn" style="left:600px;top:2004px;width:283px;height:41px">Buy It Now</div>
<div class="abs details">View Details <svg width="16" height="16" viewBox="0 0 24 24"><circle cx="12" cy="12" r="12" fill="#8a0202"/><path d="M10 7l5 5-5 5" stroke="#fff" stroke-width="3" fill="none"/></svg></div>

<!-- golf products -->
<h2 class="abs display" style="left:62px;top:2313px;font-size:31px">Golf Products</h2>
<p class="abs gp-text">Lorem ipsum dolor sit amet, consectetur adipiscing elit, sed do eiusmod tempor incididunt ut labore et dolore magna aliqua. Quis ipsum suspendisse ultrices gravida. Risus commodo viverra maecenas accumsan lacus vel facilisis. Lorem ipsum dolor sit amet, consectetur adipiscing elit, sed do eiusmod tempor incididunt ut labore et dolore magna aliqua. Quis ipsum suspendisse ultrices gravida. Risus commodo viverra maecenas accumsan lacus vel facilisis.</p>
<div class="btn" style="left:61px;top:2632px;width:196px;height:43px">View All Products</div>
<div class="abs" style="left:621px;top:2329px;width:209px;height:179px;background:radial-gradient(circle at 65% 55%,#d8d8d8 0,#6a6a6a 30%,#141414 60%,#000 100%)" role="img" aria-label="Iron club head beside a golf ball on black"></div>
<div class="abs" style="left:839px;top:2244px;width:316px;height:264px;background:radial-gradient(ellipse at 50% 50%,#eef0f6 0,#e1e4ee 55%,#fbfbfd 100%);box-shadow:0 0 8px rgba(0,0,0,.2)" role="img" aria-label="Six branded golf balls arranged in a grid"></div>
<div class="abs" style="left:621px;top:2512px;width:315px;height:264px;background:linear-gradient(90deg,#f3f3f3 0,#ebe6e6 35%,#d9d9d9 55%,#3d3d3d 72%,#e9e9e9 100%)" role="img" aria-label="Ball tube next to black drawstring bag"></div>
<div class="abs" style="left:944px;top:2512px;width:211px;height:180px;background:radial-gradient(ellipse at 50% 50%,#ffffff 0,#eeeaea 55%,#f8f8f8 100%)" role="img" aria-label="Open ball tube with lid"></div>

<!-- testimonials -->
<section class="abs testimonials"></section>
<div class="abs quote" style="left:134px;top:3012px">
  <svg width="46" height="38" viewBox="0 0 46 38" fill="#fff"><path d="M0 38V20C0 8 6 2 18 0v7c-6 2-8 6-8 11h8v20zM26 38V20C26 8 32 2 44 0v7c-6 2-8 6-8 11h8v20z"/></svg>
  <p>Lorem ipsum dolor sit amet, consectetur adipiscing elit, sed do eiusmod tempor incididunt ut labore et dolore magna aliqua. Quis ipsum suspendisse ultrices gravida. Risus commodo viverra maecenas accumsan lacus vel facilisis.</p>
  <b>- Dana Whitlow</b>
</div>
<div class="abs quote" style="left:635px;top:3012px">
  <svg width="46" height="38" viewBox="0 0 46 38" fill="#fff"><path d="M0 38V20C0 8 6 2 18 0v7c-6 2-8 6-8 11h8v20zM26 38V20C26 8 32 2 44 0v7c-6 2-8 6-8 11h8v20z"/></svg>
  <p>Lorem ipsum dolor sit amet, consectetur adipiscing elit, sed do eiusmod tempor incididunt ut labore et dolore magna aliqua. Quis ipsum suspendisse ultrices gravida. Risus commodo viverra maecenas accumsan lacus vel facilisis.</p>
  <b>- Dana Whitlow</b>
</div>

<!-- partner badges -->
<span class="abs badge" style="left:112px"></span>
<span class="abs badge" style="left:327px"></span>
<span class="abs badge" style="left:542px"></span>
<span class="abs badge" style="left:757px"></span>
<span class="abs badge" style="left:981px"></span>

<!-- footer -->
<footer class="abs footer"></footer>
<svg class="abs" style="left:115px;top:3702px" width="34" height="24" viewBox="0 0 34 24" fill="none" stroke="#fff" stroke-width="2"><rect x="1" y="1" width="32" height="22"/><path d="M1 1l16 12L33 1"/></svg>
<div class="abs news">News and promotions straight to your mailbox.</div>
<div class="abs email">Email</div>
<svg class="abs" style="left:1048px;top:3731px" width="26" height="20" viewBox="0 0 26 20" fill="none" stroke="#fff" stroke-width="2"><path d="M0 10h24M16 2l8 8-8 8"/></svg>
<div class="abs copy">© Copyrights 2023 Amber Falcon Golfing | All Rights Reserved</div>

</body>
</html>
```